Tolvik Commercial Cleaning is lookong for a new business card design.

A fresh new design that's professional and stylish. We need a serious upgrade to our business cards. I have included pictures of our existing ones. Our clients include professional individuals and business owners. We woupdblike something professional and upbeat. Please have fun and see what you come uo with.

Target Market(s)

Property managers, business owners, facility managers and other similar professionals

Industry/Entity Type

Janitorial

Contact Information for Business Card

Name, cell, office number, email, web address

Font styles to use
Sans Serif

Colors

Designer to choose colors to be used in the design.

Requirements
Must have
• please use the green color in our logo
Nice to have
• Bar code
Should not have
• Address

```html
<!DOCTYPE html>
<html lang="en">
<head>
<meta charset="utf-8">
<title>Tolvik Commercial Cleaning — Business Card</title>
<link href="https://fonts.googleapis.com/css2?family=Open+Sans:wght@400;700;800&display=swap" rel="stylesheet">
<style>
  :root {
    --stage: #232323;
    --card: #222226;
    --card-deep: #1b1b1f;
    --green: #3ab65a;
    --green-dark: #2e9447;
    --blue: #3d6fb5;
    --ink-light: #f2f2f2;
  }
  * { box-sizing: border-box; margin: 0; padding: 0; }
  html, body {
    width: 1200px; height: 780px; overflow: hidden;
    background: var(--stage);
    font-family: "Open Sans", Arial, sans-serif;
  }
  .stage {
    position: relative; width: 1200px; height: 780px;
    display: flex; align-items: center; justify-content: center; gap: 50px;
  }
  .card {
    position: relative; width: 520px; height: 300px;
    border-radius: 18px; background: var(--card);
    overflow: hidden;
    box-shadow: 0 14px 30px rgba(0,0,0,.55);
  }

  /* Front */
  .front-band {
    position: absolute; left: 0; right: 0; top: 44px; height: 212px;
    background: var(--green);
    display: flex; align-items: center; justify-content: center;
  }
  .front-wordmark {
    color: var(--green-dark); font-weight: 800; text-align: center;
    line-height: 1.05;
  }
  .front-wordmark .name-main { display: block; font-size: 72px; letter-spacing: -1px; }
  .front-wordmark .name-sub { display: block; font-size: 22px; }

  /* Back */
  .back-decor {
    position: absolute; right: -40px; top: 40px;
    font-weight: 800; font-size: 150px; line-height: 1;
    color: var(--card-deep); letter-spacing: -4px;
  }
  .back-wordmark {
    position: absolute; left: 34px; top: 36px;
    color: var(--green); font-weight: 800; line-height: 1.05;
  }
  .back-wordmark .name-main { display: block; font-size: 50px; letter-spacing: -1px; }
  .back-wordmark .name-sub { display: block; font-size: 15px; }
  .person {
    position: absolute; left: 0; top: 160px;
    display: flex; align-items: center; gap: 10px;
    font-weight: 800; font-size: 30px;
  }
  .person-marker { width: 22px; height: 30px; background: var(--green); }
  .person-first { color: var(--green); }
  .person-last { color: var(--blue); }
  .contact-list {
    position: absolute; left: 36px; top: 214px; list-style: none;
    color: var(--ink-light); font-size: 14px; line-height: 23px;
  }
  .contact-list li { display: flex; align-items: center; gap: 10px; }
  .contact-list svg { width: 14px; height: 14px; fill: var(--green); flex: none; }
</style>
</head>
<body>
<main class="stage">
  <section class="card card-front" aria-label="Business card front">
    <div class="front-band">
      <p class="front-wordmark">
        <span class="name-main">Tolvik</span>
        <span class="name-sub">Commercial Cleaning</span>
      </p>
    </div>
  </section>

  <section class="card card-back" aria-label="Business card back">
    <span class="back-decor" aria-hidden="true">Tolvik</span>
    <p class="back-wordmark">
      <span class="name-main">Tolvik</span>
      <span class="name-sub">Commercial Cleaning</span>
    </p>
    <h1 class="person">
      <span class="person-marker"></span>
      <span><span class="person-first">Marco</span> <span class="person-last">Delaney</span></span>
    </h1>
    <ul class="contact-list">
      <li>
        <svg viewBox="0 0 24 24" aria-hidden="true"><path d="M6.6 10.8a15 15 0 0 0 6.6 6.6l2.2-2.2a1 1 0 0 1 1-.25 11.4 11.4 0 0 0 3.6.57 1 1 0 0 1 1 1V20a1 1 0 0 1-1 1A17 17 0 0 1 3 4a1 1 0 0 1 1-1h3.5a1 1 0 0 1 1 1c0 1.25.2 2.45.57 3.57a1 1 0 0 1-.25 1z"/></svg>
        (555) 014-2271
      </li>
      <li>
        <svg viewBox="0 0 24 24" aria-hidden="true"><path d="M2 5h20v14H2zm2 2v.5l8 5 8-5V7zm0 2.8V17h16V9.8l-8 5z"/></svg>
        marco@tolvikcleaning.com
      </li>
      <li>
        <svg viewBox="0 0 24 24" aria-hidden="true"><path d="M12 2a10 10 0 1 0 0 20 10 10 0 0 0 0-20zm6.9 6h-3a15 15 0 0 0-1.3-3.9A8 8 0 0 1 18.9 8zM12 4c.8 1.2 1.5 2.5 1.9 4h-3.8c.4-1.5 1.1-2.8 1.9-4zM4.3 14a8 8 0 0 1 0-4h3.4a16 16 0 0 0 0 4zm.8 2h3a15 15 0 0 0 1.3 3.9A8 8 0 0 1 5.1 16zm3-8h-3a8 8 0 0 1 4.3-3.9A15 15 0 0 0 8.1 8zM12 20c-.8-1.2-1.5-2.5-1.9-4h3.8c-.4 1.5-1.1 2.8-1.9 4zm2.3-6H9.7a14 14 0 0 1 0-4h4.6a14 14 0 0 1 0 4zm.3 5.9a15 15 0 0 0 1.3-3.9h3a8 8 0 0 1-4.3 3.9zm1.7-5.9a16 16 0 0 0 0-4h3.4a8 8 0 0 1 0 4z"/></svg>
        www.tolvikcleaning.com
      </li>
    </ul>
  </section>
</main>
</body>
</html>
```